We need a cover designed for our book on parenting. The focus of this book is on the parents, not on the child! We like the idea of this title having a double meaning - insight as in gaining insights into parenting, and "in sight" as in looking inward as parents and how to improve ourselves rather than looking outward to improve our children. We would love for the cover to somehow represent this double meaning. I can upload an excerpt from the book soon over the next few days.

Reason: We are still reviewing the amazing designs! Thank you so much! :)

Target Market(s)

Parents with kids of any age from babies through adult children.

Requirements
Must have
• Title is: Harborlight Parenting
• Subtitle is: Steady Homes, Calmer Hearts Ahead
• Authors names: Lena Marsh, LCSW Oscar Marsh, Ph.D.

```html
<!DOCTYPE html>
<html lang="en">
<head>
<meta charset="utf-8">
<title>Harborlight Parenting — Book Cover</title>
<link rel="stylesheet" href="https://fonts.googleapis.com/css2?family=Lobster&family=Fira+Sans:ital,wght@0,700;1,600&display=swap">
<style>
  :root {
    --paper: #ffffff;
    --ink: #141414;
    --title-red: #e8141c;
    --title-white: #ffffff;
    --deep-red: #6e1710;
    --ember: #b8501a;
    --amber: #d9883a;
    --cream: #f3e2c8;
    --lens-dark: #1c1410;
    --umber: #4a2a14;
    --shadow: rgba(40, 8, 4, 0.55);
  }
  html, body {
    margin: 0;
    padding: 0;
    width: 800px;
    height: 1200px;
    overflow: hidden;
    background: var(--paper);
  }
  .cover {
    position: relative;
    width: 800px;
    height: 1200px;
    overflow: hidden;
    background: var(--paper);
  }
  .subtitle-band {
    position: absolute;
    inset: 0 0 auto 0;
    height: 92px;
    background: var(--paper);
    display: flex;
    align-items: center;
    justify-content: center;
  }
  .subtitle {
    margin: 0;
    font-family: "Fira Sans", sans-serif;
    font-style: italic;
    font-weight: 600;
    font-size: 36px;
    color: var(--ink);
    letter-spacing: 0.2px;
  }
  .cover-photo {
    position: absolute;
    top: 92px;
    left: 0;
    width: 800px;
    height: 1108px;
    background:
      radial-gradient(circle at 440px 620px, var(--amber) 0 85px, var(--lens-dark) 150px, var(--lens-dark) 255px, rgba(28,20,16,0) 300px),
      radial-gradient(ellipse at 90px 860px, rgba(232,190,160,0.85) 0, rgba(232,190,160,0) 260px),
      linear-gradient(180deg, rgba(0,0,0,0) 70%, var(--umber) 100%),
      linear-gradient(100deg, var(--deep-red) 0%, var(--ember) 38%, var(--amber) 62%, var(--cream) 100%);
  }
  .title {
    position: absolute;
    left: 72px;
    top: 110px;
    margin: 0;
    font-family: "Lobster", cursive;
    font-weight: 400;
    line-height: 1;
  }
  .title-lead {
    display: block;
    font-size: 100px;
    color: var(--title-red);
    text-shadow: 3px 4px 6px var(--shadow);
    letter-spacing: 1px;
  }
  .title-main {
    display: block;
    margin-top: 6px;
    font-size: 106px;
    color: var(--title-white);
    text-shadow: 3px 5px 7px var(--shadow);
  }
  .authors {
    position: absolute;
    left: 0;
    right: 0;
    bottom: 36px;
    margin: 0;
    text-align: center;
    font-family: "Fira Sans", sans-serif;
    font-weight: 700;
    font-size: 31px;
    color: var(--title-white);
    letter-spacing: 0.6px;
    text-transform: uppercase;
  }
</style>
</head>
<body>
  <main class="cover">
    <div class="cover-photo" role="img" aria-label="Photograph of a hand holding a camera lens; through the lens, silhouettes of a parent and small child holding hands against a warm sunset glow"></div>

    <header class="subtitle-band">
      <p class="subtitle">Steady Homes, Calmer Hearts Ahead</p>
    </header>

    <h1 class="title">
      <span class="title-lead">Harborlight</span>
      <span class="title-main">Parenting</span>
    </h1>

    <p class="authors">Lena Marsh &amp; LCSW &amp; Oscar Marsh &amp; Ph.D.</p>
  </main>
</body>
</html>
```